Oil and Gas Exploration and Production company needs a business card design

We need a business card design using our logo and colors in the logo. We want a mainstream design.

```html
<!DOCTYPE html>
<html lang="en">
<head>
<meta charset="utf-8">
<title>Oskerra Oil &amp; Gas – Business Card</title>
<link rel="stylesheet" href="https://fonts.googleapis.com/css2?family=Arimo:wght@400;700&display=swap">
<style>
  :root {
    --ink: #111111;
    --paper: #ffffff;
    --paper-shade: #f1f1f1;
    --gold: #d1ac3a;
    --rule: #9a9a9a;
    --stage: #e7e4df;
    --mark: #2a2320;
  }
  * { box-sizing: border-box; margin: 0; padding: 0; }
  html, body { width: 1200px; height: 780px; overflow: hidden; }
  body {
    background: var(--stage);
    font-family: "Arimo", Arial, sans-serif;
    color: var(--ink);
    display: flex;
    align-items: center;
    justify-content: center;
    gap: 80px;
  }
  .card {
    position: relative;
    width: 340px;
    height: 595px;
    border-radius: 18px;
    overflow: hidden;
    background: linear-gradient(160deg, var(--paper) 40%, var(--paper-shade));
    box-shadow: 0 10px 30px rgba(0,0,0,.18);
  }
  .brand {
    position: absolute;
    left: 0; right: 0;
    padding: 0 20px;
    display: flex;
    align-items: center;
    justify-content: center;
    gap: 10px;
    font-weight: 700;
    color: var(--ink);
    white-space: nowrap;
  }
  .brand-dot {
    width: 30px; height: 30px; border-radius: 50%;
    background: var(--mark); flex: none;
  }
  .front .brand { top: 96px; font-size: 24px; }
  .person { position: absolute; top: 232px; left: 40px; right: 40px; text-align: center; }
  .person-name { font-size: 27px; font-weight: 700; letter-spacing: .5px; }
  .person-title { font-size: 16px; color: var(--gold); margin-top: 4px; }
  .contact { position: absolute; top: 318px; left: 32px; right: 32px; text-align: center; }
  .contact-rule { height: 1px; background: var(--rule); margin: 10px 0; }
  .contact-label { font-size: 14px; font-weight: 700; font-style: italic; color: var(--gold); }
  .contact-value { font-size: 19px; margin: 2px 0 6px; }
  .address { font-size: 18px; line-height: 1.35; margin-top: 6px; }
  .band {
    position: absolute; left: 0; right: 0; height: 86px;
    background: var(--ink);
    display: flex; align-items: center; justify-content: center;
    font-size: 18px; letter-spacing: 2.5px; color: var(--paper);
    white-space: nowrap;
  }
  .band .site-name { color: var(--gold); }
  .front .band { bottom: 0; border-top: 3px solid var(--gold); box-shadow: 0 -9px 0 -6px var(--paper); }
  .back .band { top: 0; border-bottom: 3px solid var(--gold); }
  .back .brand { top: 270px; font-size: 26px; }
  .back .brand-dot { width: 34px; height: 34px; }
</style>
</head>
<body>
  <section class="card front" aria-label="Card front">
    <div class="brand"><span class="brand-dot"></span><span>Oskerra Oil &amp; Gas</span></div>
    <div class="person">
      <p class="person-name">Mara Ellison</p>
      <p class="person-title">President &amp; CEO</p>
    </div>
    <div class="contact">
      <div class="contact-rule"></div>
      <p class="contact-label">Phone</p>
      <p class="contact-value">(123) 555 0182</p>
      <p class="contact-label">Email</p>
      <p class="contact-value">info@oskerraenergy.com</p>
      <div class="contact-rule"></div>
      <p class="address">PO Box 48, Harbour Road<br>3rd Lane, Leeds</p>
    </div>
    <div class="band">www.<span class="site-name">oskerraenergy</span>.com</div>
  </section>

  <section class="card back" aria-label="Card back">
    <div class="band">www.<span class="site-name">oskerraenergy</span>.com</div>
    <div class="brand"><span class="brand-dot"></span><span>Oskerra Oil &amp; Gas</span></div>
  </section>
</body>
</html>
```